Bright Net Rally Website Design (design layout only)

We need a website design for a new nonprofit organization based in Des Moines, Iowa called Bright Net Rally. The nonprofit provides soccer training opportunities to youth soccer players looking to improve their game while also affecting the lives of the less fortunate in a positive way. While participating in the training programs the players also go out and raise money for selected charities. The organization then donates the funds. In its first 18 months we donated $10,500. We would like to see designs attempt to symbolize the mission of the nonprofit - essentially "improve you while improving someone else."

We would like to see the following features:

· A place to donate - Our intent is to have the home page linked to the donation page; a simple straight-forward process for people to give money, and make donating as painless as possible - no account needed to make a donation, credit card or e-check should be the only information needed to donate, and have it be on a single page.

· A photo gallery so people can browse the photo gallery to get a better understanding of our organization and a place to add videos and a calendar to show upcoming events

· A place for contact information and the profiles of directors and board members. This should include a spot showing all the charities the organization donates to. Also includes a news section/blog for comments and suggestions.

We want the design to revolve around the content and mission. We would really like to stress our organization as nonprofit. We would also like if the website was user friendly and easy to navigate.

The logo of our organization is uploaded

```html
<!DOCTYPE html>
<html lang="en">
<head>
<meta charset="utf-8">
<title>Bright Net Rally</title>
<link href="https://fonts.googleapis.com/css2?family=Ubuntu:wght@300;400;500;700&display=swap" rel="stylesheet">
<style>
:root{
  --green:#2d4a1e;
  --green-dark:#243d17;
  --logo-green:#6a9a3a;
  --ink:#1d1d1d;
  --muted:#5f5f5f;
  --panel:#f2f2f2;
  --field:#ececec;
  --line:#dcdcdc;
  --footer:#3a3a3a;
  --white:#ffffff;
}
*{margin:0;padding:0;box-sizing:border-box}
html,body{width:973px;height:1200px;overflow:hidden}
body{font-family:"Ubuntu",sans-serif;color:var(--ink);background:var(--white);position:relative}
.abs{position:absolute}

/* hero */
.hero{left:0;top:0;width:973px;height:452px;overflow:hidden;
  background:linear-gradient(180deg,#2e2c2e 0%,#3a4a40 18%,#3c5e34 45%,#33582a 70%,#1d3514 88%,#0e160a 100%);}
.nav-bar{left:0;top:0;width:973px;height:69px;background:rgba(30,20,20,.45);border-bottom:1px solid rgba(255,255,255,.15)}
.nav-active{left:407px;top:0;width:59px;height:69px;background:rgba(25,20,20,.65)}
.nav{top:23px;left:0;height:14px;font-size:11.5px;font-weight:500;color:var(--white);letter-spacing:.2px}
.nav span{position:absolute;white-space:nowrap}
.brand{left:81px;top:0;width:111px;height:105px;background:var(--white);border-radius:0 0 8px 8px;
  box-shadow:0 2px 4px rgba(0,0,0,.3);display:flex;flex-direction:column;align-items:center;justify-content:center;gap:6px;text-align:center}
.brand-dot{width:22px;height:22px;border-radius:50%;background:var(--logo-green)}
.brand-name{font-size:12px;font-weight:700;color:var(--logo-green);line-height:1.1;width:90px}
.hero-title{left:81px;top:164px;font-size:41px;line-height:37px;font-weight:700;color:var(--white);letter-spacing:.2px}
.btn{display:flex;align-items:center;justify-content:center;font-size:13.5px}
.btn-light{left:81px;top:303px;width:143px;height:29px;background:var(--white);color:var(--ink)}
.btn-dark{left:236px;top:303px;width:143px;height:29px;background:#111;color:var(--white)}

/* donation */
.donation{left:0;top:452px;width:973px;height:193px;background:var(--panel);border-bottom:1px solid var(--line)}
.h-donation{left:81px;top:468px;font-size:18px;font-weight:400}
.note{right:82px;top:473px;font-size:10.5px}
.divider{left:81px;top:496px;width:810px;height:1px;background:var(--line)}
.label{font-size:10.5px;color:var(--ink)}
.field{background:var(--field);border:1px solid #e0e0e0}
.select{background:var(--field);border:1px solid #e0e0e0;font-size:10.5px;color:#444;display:flex;align-items:center;padding-left:7px}
.select i{position:absolute;right:0;top:0;bottom:0;width:29px;background:var(--green-dark);display:flex;align-items:center;justify-content:center}
.select i::after{content:"";border-left:5px solid transparent;border-right:5px solid transparent;border-top:5px solid var(--white)}
.radios{left:83px;top:596px;font-size:10.5px;color:var(--muted);display:flex;gap:12px}
.radios span{display:flex;align-items:center;gap:6px}
.radios b{width:9px;height:9px;border-radius:50%;border:1px solid #d6d6d6;background:#ebebeb}
.ccv-help{left:455px;top:594px;font-size:9px;color:#888;line-height:13px}
.ccv-help u{color:#888}

/* about */
.h-about{left:81px;top:681px;font-size:23px;font-weight:400}
.about-text{left:81px;top:724px;width:570px;font-size:10.6px;line-height:14.6px;color:var(--muted);font-weight:400;letter-spacing:.15px}
.btn-green{left:81px;top:831px;width:127px;height:28px;background:var(--green);color:var(--white)}
.card{left:697px;width:196px;height:52px;border:1px solid #cfcfcf;border-radius:2px;
  background:linear-gradient(180deg,#ffffff,#e9e9e9)}
.card h3{position:absolute;left:10px;top:5px;font-size:21px;font-weight:500;color:#111}
.card p{position:absolute;left:11px;top:31px;font-size:8.8px;color:var(--muted)}
.card .badge{position:absolute;right:10px;top:6px;width:39px;height:39px;border-radius:50%;background:var(--green-dark);display:flex;align-items:center;justify-content:center}

/* features */
.photo{top:907px;width:250px;height:120px}
.ph1{left:81px;background:linear-gradient(180deg,#c9d2c4 0%,#8fa37a 55%,#5f7f3e 100%)}
.ph2{left:363px;background:linear-gradient(180deg,#a9b4a6 0%,#b84545 45%,#6f8a55 100%)}
.ph3{left:642px;background:linear-gradient(180deg,#6e5c4c 0%,#a9835e 55%,#4a4038 100%)}
.feature{top:1040px;width:260px;text-align:center}
.feature h4{font-size:15.5px;font-weight:400;margin-bottom:9px}
.feature p{font-size:10.3px;line-height:14.6px;color:var(--muted);font-weight:400;padding:0 9px}

/* footer */
.footer{left:0;top:1168px;width:973px;height:32px;background:var(--footer);color:var(--white);font-size:10px;display:flex;align-items:center;justify-content:space-between;padding:0 81px}
</style>
</head>
<body>

<div class="abs hero" role="img" aria-label="Photo of a young player leaping to kick a soccer ball on a grass field"></div>
<div class="abs nav-bar"></div>
<div class="abs nav-active"></div>
<nav class="abs nav">
  <span style="left:419px">HOME</span>
  <span style="left:483px">ABOUT US</span>
  <span style="left:568px">TEAM</span>
  <span style="left:629px">HELP</span>
  <span style="left:687px">LEAD</span>
  <span style="left:744px">GALLERY</span>
  <span style="left:822px">CONTACT US</span>
</nav>
<div class="abs brand">
  <div class="brand-dot"></div>
  <div class="brand-name">Bright Net Rally</div>
</div>
<h1 class="abs hero-title">Bright Net Rally<br>provides soccer<br>training opportunities</h1>
<div class="abs btn btn-light">Read More</div>
<div class="abs btn btn-dark">+ Get Started Now</div>

<section class="abs donation"></section>
<h2 class="abs h-donation">Donation Details</h2>
<div class="abs note">Lorem ipsum dolor *</div>
<div class="abs divider"></div>

<div class="abs label" style="left:81px;top:507px">Donation Amount *</div>
<div class="abs select" style="left:82px;top:528px;width:229px;height:27px">$0.00 Per month<i></i></div>
<div class="abs label" style="left:366px;top:507px">Name on card *</div>
<div class="abs field" style="left:366px;top:528px;width:231px;height:27px"></div>
<div class="abs label" style="left:659px;top:507px">Credit card number *</div>
<div class="abs field" style="left:660px;top:528px;width:231px;height:27px"></div>

<div class="abs label" style="left:81px;top:573px">Select your credit card type *</div>
<div class="abs radios">
  <span><b></b>NovaCard</span>
  <span><b></b>Crestpay</span>
  <span><b></b>Tablecard</span>
</div>
<div class="abs label" style="left:367px;top:573px">CCV number *</div>
<div class="abs field" style="left:366px;top:594px;width:85px;height:26px"></div>
<div class="abs ccv-help">What is CCV ?<br><u>Click here</u></div>
<div class="abs label" style="left:662px;top:573px">Expiry date *</div>
<div class="abs select" style="left:662px;top:594px;width:100px;height:26px">Jan<i></i></div>
<div class="abs select" style="left:791px;top:594px;width:100px;height:26px">2014<i></i></div>

<h2 class="abs h-about">About Bright Net Rally</h2>
<p class="abs about-text">Sed ut perspiciatis unde omnis iste natus error sit voluptatem accusantium doloremque laudantium, totam rem aperiam, eaque ipsa quae ab illo inventore veritatis et quasi architecto beatae vitae dicta sunt explicabo. Nemo enim ipsam voluptatem quia voluptas sit aspernatur aut odit aut fugit, sed quia consequuntur magni dolores eos qui ratione voluptatem sequi nesciunt. Neque porro quisquam est, qui dolorem ipsum quia dolor sit amet, consectetur adipisci velit, sed quia non numquam eius modi tempora incidunt ut labore et dolore magnam aliquam quaerat voluptatem But I must explain to you how all this mistaken idea .</p>
<div class="abs btn btn-green">Read More</div>

<div class="abs card" style="top:676px">
  <h3>Give</h3><p>Lorem ipsum dolor sit elit</p>
  <div class="badge"><svg width="18" height="16" viewBox="0 0 18 16"><path d="M9 15 L2 8 A4 4 0 0 1 9 3 A4 4 0 0 1 16 8 Z" fill="#fff"/></svg></div>
</div>
<div class="abs card" style="top:745px">
  <h3>Help</h3><p>Lorem ipsum dolor sit elit</p>
  <div class="badge"><svg width="18" height="18" viewBox="0 0 18 18"><rect x="7" y="2" width="4" height="14" fill="#fff"/><rect x="2" y="7" width="14" height="4" fill="#fff"/></svg></div>
</div>
<div class="abs card" style="top:813px">
  <h3>Lead</h3><p>Lorem ipsum dolor sit elit</p>
  <div class="badge"><svg width="18" height="18" viewBox="0 0 18 18"><path d="M5 2 V16 M5 3 H14 L11.5 6.5 L14 10 H5" fill="none" stroke="#fff" stroke-width="2" stroke-linejoin="round"/></svg></div>
</div>

<div class="abs photo ph1" role="img" aria-label="Photo of a young player celebrating on a soccer field"></div>
<div class="abs photo ph2" role="img" aria-label="Photo of a youth team in red huddling on the pitch"></div>
<div class="abs photo ph3" role="img" aria-label="Photo of many hands reaching toward a piece of fruit"></div>

<div class="abs feature" style="left:76px">
  <h4>Upcoming Events</h4>
  <p>perspiciatis unde omnis iste natus error sit tot am rem aperiam, eaque ipsa quae ab illo inventore verit atis et quasi architecto beatae vitae dicta sunt expli-cabo.</p>
</div>
<div class="abs feature" style="left:358px">
  <h4>Previous Events</h4>
  <p>perspiciatis unde omnis iste natus error sit tot am rem aperiam, eaque ipsa quae ab illo inventore verit atis et quasi architecto beatae vitae dicta sunt expli-cabo.</p>
</div>
<div class="abs feature" style="left:637px">
  <h4>Packages Delivered</h4>
  <p>perspiciatis unde omnis iste natus error sit tot am rem aperiam, eaque ipsa quae ab illo inventore verit atis et quasi architecto beatae vitae dicta sunt expli-cabo.</p>
</div>

<footer class="abs footer">
  <span>Copyrights © 2014 companyname.com - All Rights Reserved</span>
  <span>Privacy Policy &nbsp;| &nbsp;Terms Of Uses</span>
</footer>

</body>
</html>
```